BrivoTerna. Lantern of the Steady Harvest. Business card

Professional business card for BrivoTerna (Lantern of the Steady Harvest)
My rationale: Strategy-> Execution-> Results-> Value that lead to the BrivoTerna name: We put the Lantern of the Steady Harvest.
We deliver value to our customers helping them at defining a good strategy (cyan arrow). 90% of well formulated strategies fail due to poor execution so we also consider strategical execution very important (green arrow). Due to the execution we obtain the results (blue arrow). Finally, the results provide feedback to redefine strategy, and the new strategy has to be executed and new results obtained providing new feedback and on and on. It's like a wheel that finally, must create corporate value: value for shareholders, staholders, employees, providers...-

Target Market(s)

CEOs and steering comitees , invewrnent funds

Industry/Entity Type

Business Consultant

Contact Information for Business Card

Teodoro Vinsquel
CEO & Founder
teodoro.vinsquel@brivoterna-example.com
Mobile: +34 655.803.912
www.brivoterna-example.com

Colors

Designer to choose colors to be used in the design.

Requirements
Nice to have
• Nice to hace the words: Strategy, execution, results
• Nice to vave the claim: Lantern of the Steady Harvest
• The three colors should be shown:
• cyan for STRATEGY
• green for EXECUTION
• blue for RESULTS
Should not have
• Complete black background

```html
<!DOCTYPE html>
<html lang="en">
<head>
<meta charset="utf-8">
<title>BrivoTerna business card</title>
<link rel="stylesheet" href="https://fonts.googleapis.com/css2?family=Open+Sans:wght@400;700;800&display=swap">
<style>
  :root {
    --backdrop: #e6e3df;
    --card: #ffffff;
    --navy: #0b3d9c;
    --royal: #0f55b8;
    --cyan: #13a7e6;
    --green: #8cc63f;
    --ink: #3b3b3b;
    --muted: #666666;
  }
  * { margin: 0; padding: 0; box-sizing: border-box; }
  html, body {
    width: 1200px; height: 997px; overflow: hidden;
    background: var(--backdrop);
    font-family: "Open Sans", Arial, sans-serif;
  }
  .sheet {
    width: 1200px; height: 997px;
    display: flex; flex-direction: column; align-items: center; justify-content: center;
    gap: 44px;
  }
  .card {
    position: relative;
    width: 760px; height: 434px;
    background: var(--card);
    box-shadow: 0 6px 18px rgba(0,0,0,.12);
    overflow: hidden;
  }
  .accent-panel {
    position: absolute; top: 0; right: 0;
    width: 250px; height: 100%;
    background: linear-gradient(160deg, var(--navy) 0%, var(--cyan) 55%, var(--royal) 100%);
    opacity: .9;
  }
  .wordmark {
    font-weight: 800;
    color: var(--navy);
    letter-spacing: -1.5px;
    line-height: 1;
  }
  .card-front .wordmark {
    position: absolute; left: 56px; top: 112px;
    font-size: 58px;
  }
  .contact-block {
    position: absolute; left: 58px; top: 232px;
    color: var(--ink);
  }
  .person-name { font-size: 20px; font-weight: 700; color: var(--royal); }
  .person-role { font-size: 14px; color: var(--muted); margin-bottom: 12px; }
  .contact-list { list-style: none; }
  .contact-list li {
    display: flex; align-items: center; gap: 10px;
    font-size: 14.5px; line-height: 24px;
  }
  .contact-list svg { width: 15px; height: 15px; flex: none; }
  .card-back {
    display: flex; align-items: center; justify-content: center;
  }
  .card-back .wordmark { font-size: 72px; }
</style>
</head>
<body>
<main class="sheet">
  <section class="card card-front" aria-label="Business card front">
    <div class="accent-panel" role="img" aria-label="Decorative artwork in blue, cyan and green tones"></div>

    <div class="wordmark">BrivoTerna</div>

    <div class="contact-block">
      <p class="person-name">Teodoro Vinsquel</p>
      <p class="person-role">CEO &amp; Founder</p>
      <ul class="contact-list">
        <li>
          <svg viewBox="0 0 16 16" aria-hidden="true"><circle cx="8" cy="8" r="7.5" fill="var(--royal)"/><path d="M5 4.5l1.6-.4 1 2-1 .8c.5 1.1 1.3 1.9 2.4 2.4l.8-1 2 1-.4 1.6c-3 .3-6.7-3.4-6.4-6.4z" fill="#fff"/></svg>
          <span>+34 655.803.912</span>
        </li>
        <li>
          <svg viewBox="0 0 16 16" aria-hidden="true"><rect x="1" y="3" width="14" height="10" rx="1" fill="var(--royal)"/><path d="M1.5 3.8L8 9l6.5-5.2" fill="none" stroke="#fff" stroke-width="1.3"/></svg>
          <span>teodoro.vinsquel@brivoterna-example.com</span>
        </li>
        <li>
          <svg viewBox="0 0 16 16" aria-hidden="true"><circle cx="8" cy="8" r="7" fill="var(--royal)"/><g fill="none" stroke="#fff" stroke-width="1"><ellipse cx="8" cy="8" rx="3" ry="6.5"/><path d="M1.5 8h13M2.5 5h11M2.5 11h11"/></g></svg>
          <span>www.brivoterna-example.com</span>
        </li>
        <li>
          <svg viewBox="0 0 16 16" aria-hidden="true"><path d="M8 1a5 5 0 0 0-5 5c0 3.8 5 9 5 9s5-5.2 5-9a5 5 0 0 0-5-5z" fill="var(--royal)"/><circle cx="8" cy="6" r="2" fill="#fff"/></svg>
          <span>Street name, city name, zip code - 00000</span>
        </li>
      </ul>
    </div>
  </section>

  <section class="card card-back" aria-label="Business card back">
    <div class="wordmark">BrivoTerna</div>
  </section>
</main>
</body>
</html>
```